Letterhead and matching envelope design for a dental office

We need a new stationary design, letterhead and envelope #10, for a dental office in Denver area. We are called Bright Harbor Dental. We want a simple and minimalistic design but not a boring design. I wish to have one good point that makes it look professional. I have attached our logo. Feel free to use either one. I want the design for letterhead and envelope look like a "matching pair" but not look the same. The envelope doesn't have to be white and it will have an address window on bottom left.

Target Market(s)

everyone who visits dentist (adults)

Industry/Entity Type

Dental

Font styles to use
Other font styles liked:
• close to font on logo or something that matches well

Requirements
Must have
• professional
• simple, minimalistic
• unique point that stands out
Nice to have
• matching but not same design for letterhead and envelope
Should not have
• not look like all the other boring designs
• no flowery, distracting feats

```html
<!DOCTYPE html>
<html lang="en">
<head>
<meta charset="utf-8">
<title>Bright Harbor Dental – Stationery</title>
<link rel="stylesheet" href="https://fonts.googleapis.com/css2?family=Source+Sans+3:ital,wght@0,400;0,600;0,700;1,400&display=swap">
<style>
  :root {
    --green: #3bb54a;
    --leaf: #e6f2e3;
    --ink: #3a3a3a;
    --muted: #6f6f6f;
    --paper: #ffffff;
    --backdrop: #e4e4e4;
  }
  * { box-sizing: border-box; margin: 0; padding: 0; }
  html, body { width: 1200px; height: 799px; overflow: hidden; }
  body {
    background: var(--backdrop);
    font-family: "Source Sans 3", Arial, sans-serif;
    color: var(--ink);
    position: relative;
  }
  .sheet {
    position: absolute;
    background: var(--paper);
    box-shadow: 0 6px 18px rgba(0,0,0,.12);
    overflow: hidden;
  }

  /* Letterhead */
  .letterhead { left: 60px; top: 100px; width: 460px; height: 595px; }
  .brand-mark {
    position: absolute; display: flex; align-items: center; gap: 8px;
    color: var(--green); font-weight: 600; font-size: 15px; letter-spacing: .12em;
    text-transform: uppercase;
  }
  .brand-mark .dot { width: 12px; height: 12px; border-radius: 50%; background: var(--green); }
  .letterhead .brand-mark { right: 36px; top: 36px; }
  .letter-body { position: absolute; left: 48px; top: 110px; width: 340px; font-size: 10.5px; line-height: 1.45; color: var(--muted); }
  .letter-body .greeting { font-weight: 700; color: var(--ink); font-size: 12px; margin-bottom: 10px; }
  .letter-body p { margin-bottom: 10px; font-style: italic; }
  .signature { width: 90px; height: 34px; margin-top: 14px; background: #d8d8d8; border-radius: 3px; }
  .letterhead .leaves { position: absolute; left: 20px; top: 330px; }
  .letterhead .rule { position: absolute; left: 0; right: 0; top: 455px; height: 4px; background: var(--green); }
  .letterhead .rule.bottom { top: auto; bottom: 22px; height: 3px; }
  .contact { position: absolute; text-align: right; font-size: 11px; line-height: 1.45; color: var(--ink); }
  .contact .name { color: var(--green); font-weight: 700; font-size: 12px; }
  .contact .web { color: var(--green); font-size: 12px; }
  .contact .line { display: flex; justify-content: flex-end; align-items: center; gap: 4px; }
  .contact svg { flex: none; }
  .letterhead .contact { right: 36px; bottom: 40px; }

  /* Envelope back */
  .envelope-back { left: 590px; top: 95px; width: 560px; height: 244px; }
  .envelope-back .flap { position: absolute; inset: 0; }
  .envelope-back .brand-mark { left: 50%; top: 62px; transform: translateX(-50%); color: var(--paper); font-size: 13px; }
  .envelope-back .brand-mark .dot { background: var(--paper); }

  /* Envelope front */
  .envelope-front { left: 590px; top: 400px; width: 560px; height: 244px; }
  .envelope-front .leaves { position: absolute; left: 22px; top: 20px; }
  .envelope-front .rule { position: absolute; left: 0; right: 0; top: 150px; height: 4px; background: var(--green); }
  .envelope-front .brand-mark { right: 28px; top: 28px; font-size: 13px; }
  .envelope-front .contact { right: 28px; bottom: 18px; font-size: 10.5px; }
</style>
</head>
<body>

<section class="sheet letterhead" aria-label="Letterhead">
  <div class="brand-mark"><span class="dot"></span>Bright Harbor Dental</div>
  <div class="letter-body">
    <div class="greeting">Dear Mr. Adams,</div>
    <p>Thank you for choosing our practice for your family's dental care. We are pleased to confirm your upcoming visit and look forward to seeing you soon.</p>
    <p>Please arrive ten minutes early and bring your insurance card. If you need to change the time, call our front desk and we will gladly help.</p>
    <p>Our team is here to answer any questions about your treatment plan, payment options or follow-up care after your appointment.</p>
    <div class="signature" role="img" aria-label="Handwritten signature"></div>
  </div>
  <svg class="leaves" width="260" height="130" viewBox="0 0 260 130" role="img" aria-label="Faint decorative leaves">
    <rect width="260" height="130" rx="60" fill="var(--leaf)"/>
  </svg>
  <div class="rule"></div>
  <div class="contact">
    <div class="name">Bright Harbor Dental</div>
    <div>4820 Lakeview Dr, Suite 210 Arvada, CO 80002</div>
    <div class="line">
      <svg width="10" height="10" viewBox="0 0 10 10" aria-hidden="true"><circle cx="5" cy="5" r="5" fill="var(--green)"/><path d="M3.2 2.6l1 1-.5.7a3 3 0 0 0 1.9 1.9l.7-.5 1 1-.6.8C4.6 7.3 2.7 5.4 2.4 3.2z" fill="#fff"/></svg>
      720-555-0148
      <svg width="10" height="10" viewBox="0 0 10 10" aria-hidden="true"><circle cx="5" cy="5" r="5" fill="var(--green)"/><rect x="2.5" y="3.2" width="5" height="3.6" fill="#fff"/><path d="M2.5 3.2L5 5.2 7.5 3.2" stroke="var(--green)" stroke-width=".6" fill="none"/></svg>
      hello@brightharbordental.com
    </div>
    <div class="web">www.brightharbordental.com</div>
  </div>
  <div class="rule bottom"></div>
</section>

<section class="sheet envelope-back" aria-label="Envelope back">
  <svg class="flap" width="560" height="244" viewBox="0 0 560 244" aria-hidden="true">
    <path d="M0 0H560V200Q548 232 510 226L20 120Q0 114 0 96Z" fill="var(--green)"/>
  </svg>
  <div class="brand-mark"><span class="dot"></span>Bright Harbor Dental</div>
</section>

<section class="sheet envelope-front" aria-label="Envelope front">
  <svg class="leaves" width="240" height="120" viewBox="0 0 240 120" role="img" aria-label="Faint decorative leaves">
    <rect width="240" height="120" rx="56" fill="var(--leaf)"/>
  </svg>
  <div class="rule"></div>
  <div class="brand-mark"><span class="dot"></span>Bright Harbor Dental</div>
  <div class="contact">
    <div class="name">Bright Harbor Dental</div>
    <div>4820 Lakeview Dr, Suite 210 Arvada, CO 80002</div>
    <div class="web">www.brightharbordental.com</div>
  </div>
</section>

</body>
</html>
```